Design a web site for my business - Brightline Coatings Co.

We are a family business that handles design, fabrication and installation of powder coated aluminum, stainless steel and glass products. Including handrails, privacy slat screens, electric gates and pool fencing. We are based in the Whitsundays in North Queensland and service an area from Airlie Beach to Townsville.

Target Market(s)

Domestic and commercial

Industry/Entity Type

fabrication - manufacturing

Coding

Coded - Design and coding required

Number of Pages Required

5+ page

Colors
0054AA
0677BA
7BADD7
CADEEF
E8F1F8

Requirements
Must have
• photo galleries, contact page, one page for privacy screens, balustrades, glass fencing, stainless steel handrail, powder coated aluminium handrails and pool fencing

```html
<!DOCTYPE html>
<html lang="en">
<head>
<meta charset="utf-8">
<title>Our Services – Brightline Coatings Co</title>
<link href="https://fonts.googleapis.com/css2?family=Outfit:wght@300;400;500;600&family=Plus+Jakarta+Sans:wght@700;800&display=swap" rel="stylesheet">
<style>
  :root {
    --brand: #0054AA;
    --brand-mid: #0677BA;
    --brand-soft: #7BADD7;
    --brand-pale: #CADEEF;
    --page: #f3f7fc;
    --ink: #141414;
    --body: #2b2f36;
    --muted: #5a6070;
    --footer: #062c5e;
    --footer-text: #b9c8dd;
    --photo-slats: #8f9499;
    --photo-balustrade: #8a9a8c;
    --photo-pool: #7fb5cf;
    --photo-handrail: #b3ada2;
  }
  * { box-sizing: border-box; margin: 0; padding: 0; }
  html, body { width: 1200px; height: 3850px; overflow: hidden; }
  body {
    background: var(--page);
    font-family: "Outfit", sans-serif;
    color: var(--body);
    position: relative;
  }

  /* Header */
  .site-header { position: absolute; top: 0; left: 0; width: 1200px; height: 84px; }
  .brand {
    position: absolute; left: 66px; top: 32px;
    display: flex; align-items: center; gap: 8px;
    font-size: 15px; font-weight: 600; color: var(--ink);
  }
  .brand-dot { width: 12px; height: 12px; background: var(--brand); border-radius: 50%; }
  .main-nav a {
    position: absolute; top: 33px; font-size: 15px; color: var(--muted);
    text-decoration: none; line-height: 18px;
  }
  .main-nav a.active { color: var(--ink); font-weight: 600; }
  .nav-underline { position: absolute; left: 840px; top: 79px; width: 105px; height: 3px; background: #333; }

  /* Service sections */
  .service, .cta { position: absolute; left: 0; width: 1200px; text-align: center; }
  .eyebrow {
    height: 20px; line-height: 20px;
    display: flex; justify-content: center; align-items: center; gap: 14px;
    font-size: 14px; font-weight: 500; color: var(--brand);
  }
  .eyebrow::before { content: ""; width: 51px; height: 1.5px; background: var(--brand-mid); }
  .service h2, .cta h2 {
    margin-top: 13px;
    font-family: "Plus Jakarta Sans", sans-serif;
    font-weight: 800; font-size: 38px; line-height: 46px;
    text-transform: uppercase; color: var(--ink); letter-spacing: -0.3px;
  }
  .lede { margin-top: 20px; font-size: 19px; line-height: 25px; color: var(--body); }
  .media-row {
    margin-top: 65px; display: flex; gap: 28px; padding-left: 67px; text-align: left;
  }
  .photo { width: 525px; height: 350px; flex: none; }
  .detail { width: 505px; padding-top: 13px; font-size: 19.5px; line-height: 25px; }
  .features { list-style: none; margin-top: 25px; }
  .features li { position: relative; padding-left: 30px; line-height: 25px; }
  .features li::before { content: "•"; position: absolute; left: 12px; font-size: 12px; }

  .photo-slats { background: var(--photo-slats); }
  .photo-balustrade { background: var(--photo-balustrade); }
  .photo-pool { background: var(--photo-pool); }
  .photo-handrail { background: var(--photo-handrail); }

  /* CTA */
  .cta .lede { margin-top: 13px; }
  .cta-actions { margin-top: 35px; display: flex; justify-content: center; gap: 16px; }
  .btn {
    height: 57px; border-radius: 29px; display: inline-flex; align-items: center; justify-content: center;
    font-size: 19px; font-weight: 600; text-decoration: none;
  }
  .btn-primary { width: 225px; background: var(--brand); color: #fff; box-shadow: 0 6px 14px rgba(0,84,170,.3); }
  .btn-secondary { width: 169px; background: #e8f1f8; color: var(--brand); border: 1px solid var(--brand-pale); }

  /* Footer */
  .site-footer {
    position: absolute; left: 27px; top: 3459px; width: 1146px; height: 363px;
    background: var(--footer); border-radius: 30px; color: var(--footer-text);
  }
  .footer-brand {
    position: absolute; left: 66px; top: 66px;
    display: flex; align-items: center; gap: 8px;
    font-size: 15px; font-weight: 600; color: #fff;
  }
  .footer-brand .brand-dot { background: var(--brand-soft); }
  .footer-tagline { position: absolute; left: 66px; top: 150px; width: 290px; font-size: 17px; line-height: 27px; }
  .footer-col { position: absolute; top: 52px; }
  .footer-col h3 { font-size: 19px; font-weight: 600; color: #fff; line-height: 24px; letter-spacing: .3px; }
  .footer-col ul { list-style: none; margin-top: 21px; }
  .footer-col li { font-size: 15px; line-height: 28px; }
  .col-services { left: 430px; }
  .col-company { left: 624px; }
  .col-contact { left: 819px; }
  .copyright { position: absolute; left: 0; right: 0; top: 320px; text-align: center; font-size: 15px; }
</style>
</head>
<body>
  <header class="site-header">
    <div class="brand"><span class="brand-dot"></span>Brightline Coatings Co</div>
    <nav class="main-nav">
      <a href="#" style="left:672px">Home</a>
      <a href="#" style="left:751px">About Us</a>
      <a href="#" class="active" style="left:849px">Our Services</a>
      <a href="#" style="left:973px">Gallery</a>
      <a href="#" style="left:1061px">Contact Us</a>
    </nav>
    <div class="nav-underline"></div>
  </header>

  <main>
    <section class="service" style="top:199px">
      <div class="eyebrow">Privacy Slat Screens</div>
      <h2>Modern Privacy<br>With Architectural Style</h2>
      <p class="lede">Custom aluminium privacy slat screens designed to enhance security,<br>airflow, and contemporary aesthetics.</p>
      <div class="media-row">
        <div class="photo photo-slats" role="img" aria-label="Photo: dark aluminium slat privacy screen on a tiled balcony"></div>
        <div class="detail">
          <p>Privacy slat screens offer the perfect balance of privacy, ventilation, and modern design. Ideal for residential homes, commercial properties, patios, and boundary fencing, our custom-made aluminium slat systems are manufactured to suit your exact requirements.</p>
          <ul class="features">
            <li>Increased Privacy</li><li>Modern Architectural Appearance</li><li>Powder Coated Finishes</li>
            <li>Low Maintenance</li><li>Corrosion Resistant</li><li>Custom Colours &amp; Sizes</li><li>Built for Coastal Conditions</li>
          </ul>
        </div>
      </div>
    </section>

    <section class="service" style="top:927px">
      <div class="eyebrow">Balustrades</div>
      <h2>Elegant Balustrades<br>Built for Safety &amp; Style</h2>
      <p class="lede">Premium glass and aluminium balustrade systems that enhance<br>modern living spaces.</p>
      <div class="media-row">
        <div class="photo photo-balustrade" role="img" aria-label="Photo: frameless glass balustrade on a stone-clad terrace"></div>
        <div class="detail">
          <p>Our balustrade systems combine safety, durability, and contemporary design. Whether for staircases, balconies, decks, or commercial buildings, we provide custom solutions that maximize views while meeting Australian safety standards.</p>
          <ul class="features">
            <li>Frameless Glass Options</li><li>Semi-Frameless Systems</li><li>Aluminium Balustrades</li>
            <li>Stainless Steel Components</li><li>Custom Designs</li><li>Residential &amp; Commercial</li>
          </ul>
        </div>
      </div>
    </section>

    <section class="service" style="top:1653px">
      <div class="eyebrow">Glass Pool Fencing</div>
      <h2>Safe Stylish Crystal Clear</h2>
      <p class="lede">Premium frameless and semi-frameless glass pool fencing<br>designed for modern outdoor living.</p>
      <div class="media-row">
        <div class="photo photo-pool" role="img" aria-label="Photo: backyard pool surrounded by frameless glass fencing"></div>
        <div class="detail">
          <p>Create an open, luxurious pool area without compromising safety. Our glass fencing systems provide unobstructed views while meeting all Australian pool safety regulations.</p>
          <ul class="features">
            <li>Frameless Design</li><li>Safety Certified</li><li>Toughened Glass</li>
            <li>Corrosion Resistant Hardware</li><li>Minimal Maintenance</li><li>Coastal Grade Materials</li>
          </ul>
        </div>
      </div>
    </section>

    <section class="service" style="top:2334px">
      <div class="eyebrow">Stainless Steel Handrails</div>
      <h2>Strength Meets Sophistication</h2>
      <p class="lede">Custom stainless steel handrails designed for<br>durability, safety, and timeless style.</p>
      <div class="media-row">
        <div class="photo photo-handrail" role="img" aria-label="Photo: stainless steel handrail on a waterfront terrace"></div>
        <div class="detail">
          <p>Our stainless steel handrails provide superior strength while complementing modern residential and commercial architecture. Every system is custom fabricated for a flawless fit.</p>
          <ul class="features">
            <li>Marine Grade Stainless Steel</li><li>Indoor &amp; Outdoor Applications</li><li>Corrosion Resistant</li>
            <li>Modern Finish</li><li>Custom Fabrication</li><li>Commercial Grade Quality</li>
          </ul>
        </div>
      </div>
    </section>

    <section class="cta" style="top:3015px">
      <div class="eyebrow">Get In Touch</div>
      <h2>Get In Touch<br>Let's Build Something<br>Exceptional</h2>
      <p class="lede">Tell us about your project and we'll get back to you with<br>a free, no-obligation quote.</p>
      <div class="cta-actions">
        <a href="#" class="btn btn-primary">Request Free Quote</a>
        <a href="#" class="btn btn-secondary">View Projects</a>
      </div>
    </section>
  </main>

  <footer class="site-footer">
    <div class="footer-brand"><span class="brand-dot"></span>Brightline Coatings Co</div>
    <p class="footer-tagline">Family-owned fabrication of aluminium and stainless steel handrails, glass.</p>
    <div class="footer-col col-services">
      <h3>SERVICES</h3>
      <ul><li>Glass Balustrades</li><li>Pool Fencing</li><li>Handrails</li><li>Electric Gates</li><li>Slat Screens</li></ul>
    </div>
    <div class="footer-col col-company">
      <h3>COMPANY</h3>
      <ul><li>About Us</li><li>Our Projects</li><li>Request a Quote</li><li>Service Areas</li></ul>
    </div>
    <div class="footer-col col-contact">
      <h3>CONTACT</h3>
      <ul><li>0700 000 000</li><li>info@brightlinecoatings.com.au</li><li>Mon–Fri: 7am – 4pm</li><li>Sat: By appointment</li></ul>
    </div>
    <p class="copyright">© 2026 Brightline Coatings Co. All rights reserved</p>
  </footer>
</body>
</html>
```